Business Card Update, need to bring life to the card, two sided color

We need a new business card design, are moving and changing addresses and need a new look, we have the logos already attached but need a new style moving forward. Can incorporate the color of the logo (The Green) as well, maybe a solid back? We deal with safety products revolving around static electricity and safety lighting. Would like to keep same font in second logo as well.

Target Market(s)

Electrical Safety, Lighting

Contact Information for Business Card

Dale Fenwick
Vice President
Office: 770-555-4821
Cell: 770-555-3067
dale@tkfenwick.example
www.tkfenwick.example
4700 West Harbor Boulevard
Suite #150
Roswell, GA 30076

Font styles to use
Serif
Sans Serif

Requirements
Must have
• Since 1918
Nice to have
• Could use the 100 Year Logo for back of card, would like the back of card to be the same green as logo.
Should not have
• No black cards please.

```html
<!DOCTYPE html>
<html lang="en">
<head>
<meta charset="utf-8">
<title>T.K. Fenwick Business Card</title>
<link rel="stylesheet" href="https://fonts.googleapis.com/css2?family=Roboto:wght@400;500;700;900&display=swap">
<style>
  :root {
    --brand-green: #069a58;
    --paper-white: #ffffff;
    --backdrop: #e9ebea;
    --card-shadow: rgba(0, 0, 0, 0.18);
  }
  * { box-sizing: border-box; margin: 0; padding: 0; }
  html, body {
    width: 1200px; height: 768px; overflow: hidden;
    background: var(--backdrop);
    font-family: "Roboto", Arial, sans-serif;
  }
  .stage {
    width: 1200px; height: 768px;
    display: flex; align-items: center; justify-content: center; gap: 60px;
  }
  .card {
    position: relative;
    width: 520px; height: 297px;
    border-radius: 22px;
    overflow: hidden;
    background: var(--brand-green);
    box-shadow: 0 12px 30px var(--card-shadow);
    color: var(--paper-white);
  }

  /* Back side */
  .card-back .brand-mark {
    position: absolute; left: 0; right: 0; top: 90px;
    display: flex; align-items: center; justify-content: center; gap: 14px;
  }
  .card-back .brand-dot {
    width: 44px; height: 44px; border-radius: 50%;
    background: var(--paper-white);
  }
  .card-back .brand-name {
    font-size: 34px; font-weight: 700; letter-spacing: 0.5px;
  }
  .card-back .since {
    position: absolute; left: 0; right: 0; top: 150px;
    text-align: center; font-size: 13px; font-weight: 500; letter-spacing: 3px;
  }
  .card-back .back-url {
    position: absolute; left: 0; right: 0; bottom: 40px;
    text-align: center; font-size: 14px; letter-spacing: 5px;
  }

  /* Front side */
  .front-field { position: absolute; inset: 0; }
  .front-brand {
    position: absolute; left: 34px; top: 92px; width: 220px;
    color: var(--brand-green); text-align: center;
  }
  .front-brand .brand-row {
    display: flex; align-items: center; justify-content: center; gap: 10px;
  }
  .front-brand .brand-dot {
    width: 28px; height: 28px; border-radius: 50%; background: var(--brand-green);
  }
  .front-brand .brand-name { font-size: 27px; font-weight: 700; }
  .front-brand .brand-sub {
    margin-top: 4px; font-size: 11.5px; font-weight: 700; letter-spacing: 0.4px;
  }
  .front-brand .since {
    margin-top: 6px; font-size: 11px; font-weight: 500; letter-spacing: 2px;
  }
  .contact-block {
    position: absolute; left: 318px; top: 40px; width: 192px;
  }
  .person-name { font-size: 22px; font-weight: 700; letter-spacing: 0.4px; line-height: 1.05; }
  .person-title { font-size: 13px; font-weight: 500; margin-bottom: 14px; }
  .address { font-size: 12px; line-height: 1.3; margin-bottom: 12px; }
  .contact-list { list-style: none; font-size: 12px; line-height: 1.55; }
  .contact-list li { display: flex; align-items: center; gap: 8px; white-space: nowrap; }
  .contact-list svg { width: 12px; height: 12px; flex: none; fill: var(--paper-white); }
</style>
</head>
<body>
<main class="stage">

  <section class="card card-back" aria-label="Card back">
    <div class="brand-mark">
      <span class="brand-dot"></span>
      <span class="brand-name">T.K. Fenwick</span>
    </div>
    <p class="since">SINCE 1918</p>
    <p class="back-url">www.tkfenwick.example</p>
  </section>

  <section class="card card-front" aria-label="Card front">
    <svg class="front-field" viewBox="0 0 520 297" aria-hidden="true">
      <circle cx="40" cy="160" r="262" fill="#ffffff"/>
    </svg>

    <div class="front-brand">
      <div class="brand-row">
        <span class="brand-dot"></span>
        <span class="brand-name">T.K. Fenwick</span>
      </div>
      <p class="brand-sub">Manufacturing Company, Inc.</p>
      <p class="since">SINCE 1918</p>
    </div>

    <div class="contact-block">
      <h1 class="person-name">Dale Fenwick</h1>
      <p class="person-title">Vice President</p>
      <p class="address">4700 West Harbor Boulevard<br>Suite #150<br>Roswell, GA 30076</p>
      <ul class="contact-list">
        <li><svg viewBox="0 0 12 12"><path d="M2.5 0.5l2 2.2-1 1.3c.6 1.6 1.8 2.9 3.5 3.5l1.3-1 2.2 2-.9 2c-4.8-.3-8.6-4.1-8.9-8.9z"/></svg>770 555 4821</li>
        <li><svg viewBox="0 0 12 12"><path d="M3 0h6v12H3zM4 1.5v8h4v-8z"/></svg>770 555 3067</li>
        <li><svg viewBox="0 0 12 12"><path d="M3 0h6v3H3zM1 4h10v5H9v3H3V9H1zM4 8v3h4V8z"/></svg>770 555 2290</li>
        <li><svg viewBox="0 0 12 12"><path d="M0 2h12v8H0zM1 3l5 3.5L11 3v-.1H1z" fill-rule="evenodd"/></svg>dale@tkfenwick.example</li>
        <li><svg viewBox="0 0 12 12"><circle cx="6" cy="6" r="5.5"/></svg>www.tkfenwick.example</li>
      </ul>
    </div>
  </section>

</main>
</body>
</html>
```